Tolbek cards

I want a simple business card that pops.
Logo on one side.
On side two i want.
"Are you thinking about a new building on your property, or renovating an existing structure? Contact".....
Owners Name: Dale Whitacre
Owners Phone number: 610-555-0187
Address:4076 Copper Ridge RD, Millbrook, PA 17390
Committed to Quality, Service, and Integrity

```html
<!DOCTYPE html>
<html lang="en">
<head>
<meta charset="utf-8">
<title>Tolbek Builders LLC – Business Cards</title>
<link href="https://fonts.googleapis.com/css2?family=Archivo:wght@700&family=Lato:wght@400;700;900&display=swap" rel="stylesheet">
<style>
  :root {
    --bg: #e6e4e2;
    --card: #ffffff;
    --brown-dark: #4a3526;
    --brown-mid: #7a5c44;
    --brown-light: #a88a6e;
    --text: #3d2c20;
    --rule: #8c6f57;
  }
  * { margin: 0; padding: 0; box-sizing: border-box; }
  html, body { width: 1200px; height: 689px; overflow: hidden; }
  body {
    background: var(--bg);
    font-family: "Lato", sans-serif;
    color: var(--text);
    position: relative;
  }
  .card {
    position: absolute;
    top: 190px;
    width: 520px;
    height: 300px;
    background: var(--card);
    border-radius: 22px;
    overflow: hidden;
    box-shadow: 0 2px 6px rgba(0,0,0,0.08);
  }
  .card--front { left: 45px; }
  .card--back { left: 635px; }

  /* Front */
  .brand {
    position: absolute;
    inset: 0;
    display: flex;
    align-items: center;
    justify-content: center;
    gap: 18px;
  }
  .brand__mark {
    flex: none;
    width: 40px; height: 40px;
    background: var(--brown-mid);
  }
  .brand__name {
    display: flex;
    flex-direction: column;
    align-items: center;
    font-family: "Lato", sans-serif;
    font-weight: 900;
    text-transform: uppercase;
    color: var(--brown-dark);
    line-height: 1;
    white-space: nowrap;
  }
  .brand__word { font-size: 64px; letter-spacing: 2px; }
  .brand__suffix { font-size: 24px; letter-spacing: 3px; margin-top: 4px; }

  /* Back */
  .back__brand {
    position: absolute;
    top: 38px; right: 40px;
    font-weight: 900;
    font-size: 26px;
    text-transform: uppercase;
    color: var(--brown-dark);
    letter-spacing: 1px;
  }
  .back__rule {
    position: absolute;
    top: 92px; left: 40px; right: 40px;
    height: 1px;
    background: var(--rule);
  }
  .tagline {
    position: absolute;
    top: 110px; left: 40px;
    width: 300px;
    font-family: "Archivo", sans-serif;
    font-weight: 700;
    font-size: 11.5px;
    line-height: 1.3;
    text-transform: uppercase;
    letter-spacing: 0.5px;
    color: var(--brown-mid);
  }
  .contact {
    position: absolute;
    left: 40px; top: 178px;
    width: 440px;
  }
  .contact__name {
    font-weight: 900;
    font-size: 20px;
    text-transform: uppercase;
    color: var(--brown-dark);
    letter-spacing: 0.5px;
  }
  .contact__role {
    display: flex;
    align-items: center;
    gap: 6px;
    font-size: 12px;
    margin-top: 2px;
  }
  .contact__role::after {
    content: "";
    flex: 1;
    height: 1px;
    background: var(--rule);
  }
  .contact__company {
    margin-top: 8px;
    font-weight: 700;
    font-size: 11.5px;
    color: var(--brown-dark);
  }
  .contact__address { font-size: 11.5px; margin-top: 1px; }
  .contact__phone {
    display: flex;
    align-items: center;
    gap: 4px;
    margin-top: 3px;
    font-weight: 900;
    font-size: 16px;
    color: var(--brown-dark);
  }
  .edge-band {
    position: absolute;
    left: 0; right: 0; bottom: 0;
    height: 7px;
    background: linear-gradient(90deg, var(--brown-dark), var(--brown-light));
  }
</style>
</head>
<body>
  <section class="card card--front" aria-label="Card front">
    <div class="brand">
      <span class="brand__mark"></span>
      <span class="brand__name">
        <span class="brand__word">Tolbek</span>
        <span class="brand__suffix">Builders LLC</span>
      </span>
    </div>
  </section>

  <section class="card card--back" aria-label="Card back">
    <div class="back__brand">Tolbek</div>
    <div class="back__rule"></div>
    <p class="tagline">Are you thinking about a new building on your property, or renovating an existing structure? Contact.....</p>
    <div class="contact">
      <div class="contact__name">Dale Whitacre</div>
      <div class="contact__role">Owner</div>
      <div class="contact__company">Tolbek Builders LLC</div>
      <div class="contact__address">4076 Copper Ridge RD, Millbrook, PA 17390</div>
      <div class="contact__phone">
        <svg width="14" height="14" viewBox="0 0 24 24" aria-hidden="true">
          <path fill="var(--brown-dark)" d="M6.6 10.8a15.1 15.1 0 0 0 6.6 6.6l2.2-2.2a1 1 0 0 1 1-.25 11.4 11.4 0 0 0 3.6.57 1 1 0 0 1 1 1V20a1 1 0 0 1-1 1A17 17 0 0 1 3 4a1 1 0 0 1 1-1h3.5a1 1 0 0 1 1 1c0 1.25.2 2.45.57 3.57a1 1 0 0 1-.25 1z"/>
        </svg>
        610-555-0187
      </div>
    </div>
    <div class="edge-band"></div>
  </section>
</body>
</html>
```